The Aldermoor- outdoor banner

This should be a horizontal banner. It should have the logos attached incorporated and the following details
Coming Spring 2025: The Aldermoor - Exclusive Luxury Condos
Listed by Marisol Quennell | Fairlight Realty
Construction by Stonegate Build Group
Unveil the height of luxury living with The Aldermoor, a new condo building in East Boston, set for completion in Spring 2025. Experience a standard of elegance and sophistication like never before.
For more information and inquiries, please contact:
Marisol Quennell
Phone: (617) 430-9162
Email: marisol@fairlightprops.com
The banner should be very classy incorporting gold and navy very classic fonts. The Aldermoor should look very classy and exclusive. The stonegate build group logo should be smaller. It should not include their phone number and instagram handle only the name of the company. Herringbone pattern in the background would be great. This is going outside the building to advertise pre construction units

```html
<!DOCTYPE html>
<html lang="en">
<head>
<meta charset="utf-8">
<title>The Aldermoor – Coming Spring 2025</title>
<link rel="stylesheet" href="https://fonts.googleapis.com/css2?family=Cinzel:wght@400;600;700&family=Questrial&family=Montserrat:wght@400;600;700&display=swap">
<style>
  :root {
    --navy-deep: #0f1640;
    --navy: #1a2656;
    --navy-light: #26366e;
    --gold-dark: #c9820f;
    --gold: #f2b51c;
    --gold-light: #fbe27a;
    --silver: #e6e6ea;
    --white: #ffffff;
  }
  html, body {
    margin: 0;
    padding: 0;
    width: 1200px;
    height: 600px;
    overflow: hidden;
    background: var(--navy-deep);
  }
  .banner {
    position: relative;
    width: 1200px;
    height: 600px;
    overflow: hidden;
    background: radial-gradient(ellipse at 45% 35%, var(--navy-light) 0%, var(--navy) 40%, var(--navy-deep) 100%);
    font-family: "Questrial", sans-serif;
    color: var(--white);
  }
  .banner__bands {
    position: absolute;
    inset: 0;
  }
  .headline {
    position: absolute;
    top: 28px;
    left: 0;
    width: 1200px;
    margin: 0;
    text-align: center;
    font-family: "Cinzel", serif;
    font-weight: 400;
    font-size: 84px;
    letter-spacing: 3px;
    color: var(--silver);
    text-shadow: 2px 3px 4px rgba(0,0,0,0.55);
  }
  .title-block {
    position: absolute;
    left: 110px;
    top: 132px;
    width: 630px;
    text-align: center;
  }
  .title-block__the {
    display: flex;
    align-items: center;
    gap: 16px;
    font-family: "Cinzel", serif;
    font-weight: 700;
    font-size: 38px;
    color: var(--gold);
    text-shadow: 2px 2px 3px rgba(0,0,0,0.6);
    line-height: 1;
  }
  .rule {
    flex: 1;
    height: 2px;
    background: linear-gradient(90deg, var(--gold-dark), var(--gold-light), var(--gold));
  }
  .title-block__name {
    margin: 10px 0 0;
    font-family: "Cinzel", serif;
    font-weight: 700;
    font-size: 92px;
    line-height: 1;
    letter-spacing: 2px;
    background: linear-gradient(180deg, var(--gold-light) 0%, var(--gold) 55%, var(--gold-dark) 100%);
    -webkit-background-clip: text;
    background-clip: text;
    color: transparent;
    filter: drop-shadow(2px 3px 3px rgba(0,0,0,0.6));
  }
  .title-block__tagline {
    margin: 12px 0 0;
    font-family: "Cinzel", serif;
    font-weight: 600;
    font-size: 40px;
    line-height: 1;
    color: var(--gold);
    text-shadow: 2px 2px 3px rgba(0,0,0,0.6);
  }
  .title-block__base {
    margin-top: 14px;
    height: 2px;
    background: linear-gradient(90deg, var(--gold-dark), var(--gold-light), var(--gold));
  }
  .credit {
    position: absolute;
    text-align: center;
    font-family: "Montserrat", sans-serif;
  }
  .credit__label {
    font-size: 13px;
    font-weight: 600;
    letter-spacing: 0.5px;
  }
  .credit__name {
    font-size: 17px;
    font-weight: 700;
    letter-spacing: 0.5px;
  }
  .credit--listing {
    left: 790px;
    top: 160px;
    width: 200px;
  }
  .credit--builder {
    left: 1000px;
    top: 182px;
    width: 170px;
  }
  .brand-mark {
    display: block;
    margin: 0 auto;
  }
  .brand-name {
    font-family: "Cinzel", serif;
    font-weight: 600;
    color: var(--white);
  }
  .brand-name--realty {
    margin-top: 8px;
    font-size: 20px;
    letter-spacing: 1px;
  }
  .brand-name--builder {
    margin-top: 28px;
    font-size: 13px;
    letter-spacing: 0.5px;
  }
  .intro {
    position: absolute;
    left: 0;
    top: 360px;
    width: 1200px;
    margin: 0;
    text-align: center;
    font-size: 24px;
    line-height: 30px;
    letter-spacing: 0.4px;
  }
  .intro__lead { display: block; }
  .intro__closing { display: block; margin-top: 4px; }
  .contact {
    position: absolute;
    left: 0;
    top: 498px;
    width: 1200px;
    text-align: center;
  }
  .contact__prompt {
    font-family: "Questrial", sans-serif;
    font-size: 17px;
    letter-spacing: 0.3px;
    margin: 0 0 12px;
  }
  .contact__row {
    display: flex;
    justify-content: center;
    align-items: center;
    gap: 10px;
    font-family: "Montserrat", sans-serif;
    font-weight: 700;
    font-size: 22px;
    letter-spacing: 0.3px;
  }
  .contact__name { margin-right: 6px; }
  .contact__phone { margin-right: 6px; }
  .contact__icon { width: 30px; height: 30px; }
  .gold-band {
    position: absolute;
    left: 0;
    bottom: 0;
    width: 1200px;
    height: 10px;
    background: linear-gradient(90deg, var(--gold-dark), var(--gold), var(--gold-light), var(--gold), var(--gold-dark));
  }
</style>
</head>
<body>
<main class="banner">
  <svg class="banner__bands" width="1200" height="600" viewBox="0 0 1200 600" aria-hidden="true">
    <polygon points="0,250 0,600 180,600" fill="#0c1238" opacity="0.55"/>
    <polygon points="0,330 0,420 200,600 280,600" fill="#2a3a78" opacity="0.18"/>
    <polygon points="1000,0 1200,0 1200,200" fill="#2a3a78" opacity="0.2"/>
    <polygon points="880,0 940,0 1200,300 1200,370" fill="#2a3a78" opacity="0.15"/>
    <polygon points="1050,600 1200,600 1200,430" fill="#0c1238" opacity="0.5"/>
    <rect x="0" y="462" width="1200" height="120" fill="#0c1238" opacity="0.25"/>
  </svg>

  <h1 class="headline">Coming Spring 2025</h1>

  <section class="title-block">
    <div class="title-block__the"><span class="rule"></span>The<span class="rule"></span></div>
    <h2 class="title-block__name">Aldermoor</h2>
    <p class="title-block__tagline">Exclusive Luxury Condos</p>
    <div class="title-block__base"></div>
  </section>

  <div class="credit credit--listing">
    <div class="credit__label">LISTED BY</div>
    <div class="credit__name">Marisol Quennell</div>
    <svg class="brand-mark" width="64" height="64" viewBox="0 0 64 64" aria-hidden="true" style="margin-top:18px">
      <circle cx="32" cy="32" r="29" fill="none" stroke="#ffffff" stroke-width="2.5"/>
    </svg>
    <div class="brand-name brand-name--realty">FAIRLIGHT REALTY</div>
  </div>

  <div class="credit credit--builder">
    <div class="credit__label">CONSTRUCTION BY</div>
    <div class="brand-name brand-name--builder">STONEGATE BUILD GROUP</div>
  </div>

  <p class="intro">
    <span class="intro__lead">Unveil the height of luxury living with The Aldermoor, a new condo<br>building in East Boston, set for completion in Spring 2025.</span>
    <span class="intro__closing">Experience a standard of elegance and sophistication like never before.</span>
  </p>

  <section class="contact">
    <p class="contact__prompt">FOR MORE INFORMATION AND INQUIRIES, PLEASE CONTACT</p>
    <div class="contact__row">
      <span class="contact__name">MARISOL QUENNELL</span>
      <svg class="contact__icon" viewBox="0 0 30 30" aria-label="Phone">
        <circle cx="15" cy="15" r="13.5" fill="none" stroke="#f2b51c" stroke-width="2"/>
        <path d="M10.5 9.5 l2.5 -0.5 l1.3 3 l-1.5 1.2 a7 7 0 0 0 3.5 3.5 l1.2 -1.5 l3 1.3 l-0.5 2.5 a9 9 0 0 1 -9.5 -9.5z" fill="none" stroke="#ffffff" stroke-width="1.4" stroke-linejoin="round"/>
      </svg>
      <span class="contact__phone">(617) 430-9162</span>
      <svg class="contact__icon" viewBox="0 0 30 30" aria-label="Email">
        <circle cx="15" cy="15" r="13.5" fill="none" stroke="#f2b51c" stroke-width="2"/>
        <rect x="8.5" y="10" width="13" height="10" rx="1.5" fill="none" stroke="#ffffff" stroke-width="1.4"/>
        <path d="M11 14 h8" stroke="#ffffff" stroke-width="1.4"/>
      </svg>
      <span class="contact__email">MARISOL@FAIRLIGHTPROPS.COM</span>
    </div>
  </section>

  <div class="gold-band"></div>
</main>
</body>
</html>
```